Fitness Centre/Personal Trainer Business Card

We need a business card design for a company based in Singapore called 'Vigor Ledger'.

We are a team of Personal Trainers and we are planning to open our new training facility.

This design will also be printed/painted on the walls in our gym.

We are a new breed of personal trainers who take fitness seriously and holistically. We do not merely train our clients to be big and muscular.

We believe in wholeness. In our opinion, fitness should include: strength, speed, flexibility, mobility, stamina & agility. These are what we train for. Of course, nutrition/diet is key.

We use fitness tools such as kettlebells, QVL, Pylometric boxes, battling ropes, clubbells, medicine balls, bulgarian bags etc - functional and non-bulky tools.

I currently have a Facebook page 'Vigor Ledger SG' which shows a logo of a kettlebell. But my business focus has since changed.

Services provided:
- Kettlebell Sport Preparation
- Calisthenics Training
- Corrective Exercises
- Sports Strength & Conditioning
- 28 days Weight Loss Program
- Myofascial Rehab Therapy
- Sports/Thai Massage

Main colors for the design should be BLACK & YELLOW. We envision a design which is able to protray the holistic view we take on fitness. Also it should somewhat appeal to the ladies and not intimidate them.

Target Market(s)

People between 18-35 years old. Students and working class alike.

Industry/Entity Type

Training

Requirements
Must have
• Name: Marcus Obadiah Lim
Fitness Coach
Corrective Exercise Specialist
M: +65 9437 2065
E: marcus@sgvigorledger-example.com

Double-sided please.
Nice to have
• "What is your vigor ledger?"

```html
<!DOCTYPE html>
<html lang="en">
<head>
<meta charset="utf-8">
<title>Vigor Ledger – Business Card</title>
<link href="https://fonts.googleapis.com/css2?family=Open+Sans:wght@400;600;700&display=swap" rel="stylesheet">
<style>
  :root {
    --board: #b9b9b9;
    --board-light: #e4e4e4;
    --card-white: #ffffff;
    --card-black: #000000;
    --ink: #1a1a1a;
    --ink-soft: #3a3a3a;
    --yellow: #f3d80f;
    --yellow-text: #f5d000;
    --rule: #c8c8c8;
    --ghost: #ececec;
  }
  * { box-sizing: border-box; margin: 0; padding: 0; }
  html, body { width: 1200px; height: 719px; overflow: hidden; }
  body {
    position: relative;
    font-family: "Open Sans", Arial, sans-serif;
    background: radial-gradient(ellipse at 55% 45%, var(--board-light) 0%, var(--board) 85%);
    color: var(--ink);
  }
  .card {
    position: absolute;
    width: 539px;
    height: 307px;
    overflow: hidden;
    border: 1px solid #9a9a9a;
  }
  .card--front { left: 49px; top: 222px; background: var(--card-white); }
  .card--back-dark { left: 615px; top: 39px; background: var(--card-black); }
  .card--back-light { left: 615px; top: 375px; background: var(--card-white); }

  /* brand mark: plain disc + name */
  .brand { position: absolute; text-align: center; }
  .brand__disc {
    display: block;
    margin: 0 auto;
    border-radius: 50%;
    background: var(--yellow);
  }
  .brand__name { display: block; font-weight: 700; line-height: 1.1; margin-top: 14px; white-space: nowrap; }

  .card--front .brand { left: 30px; top: 52px; width: 200px; }
  .card--front .brand__disc { width: 140px; height: 140px; }
  .card--front .brand__name { font-size: 26px; color: var(--ink); }

  .card--back-dark .brand { left: 30px; top: 48px; width: 190px; }
  .card--back-dark .brand__disc { width: 140px; height: 140px; }
  .card--back-dark .brand__name { font-size: 26px; color: var(--yellow); }

  /* front card */
  .athlete-figure {
    position: absolute; left: 282px; top: 30px; width: 225px; height: 250px;
    background: radial-gradient(ellipse at center, var(--ghost) 0%, rgba(236,236,236,0.4) 55%, rgba(255,255,255,0) 75%);
  }
  .divider { position: absolute; left: 258px; top: 62px; width: 2px; height: 178px; background: var(--rule); }
  .contact { position: absolute; left: 280px; top: 72px; }
  .contact__name { font-size: 18px; font-weight: 700; color: var(--ink); }
  .contact__role { font-size: 14px; line-height: 19px; color: var(--ink-soft); }
  .contact__list { list-style: none; margin-top: 22px; }
  .contact__list li { display: flex; align-items: center; gap: 6px; font-size: 13px; line-height: 24px; color: var(--ink-soft); white-space: nowrap; }
  .contact__list svg { width: 12px; height: 12px; flex: none; }
  .front-band { position: absolute; left: 0; bottom: 0; width: 539px; height: 12px; }

  /* dark back */
  .services-title { font-weight: 700; font-size: 19px; }
  .card--back-dark .services-title { position: absolute; left: 277px; top: 24px; color: var(--yellow-text); }
  .service-list { list-style: none; }
  .card--back-dark .service-list { position: absolute; left: 277px; top: 64px; }
  .card--back-dark .service-list li { font-size: 15.5px; line-height: 27px; color: var(--yellow-text); }
  .service-list li::before { content: "\2022"; margin-right: 3px; }
  .tagline-question { position: absolute; left: 0; width: 100%; text-align: center; font-weight: 700; letter-spacing: 1px; }
  .card--back-dark .tagline-question { top: 262px; padding-left: 60px; font-size: 16px; color: #ffffff; }

  /* light back */
  .ghost-disc {
    position: absolute; left: 175px; top: 18px; width: 175px; height: 175px;
    border-radius: 50%; background: var(--yellow); opacity: 0.12;
  }
  .card--back-light .services-title { position: absolute; left: 0; width: 100%; text-align: center; top: 68px; color: var(--ink); }
  .service-grid { position: absolute; left: 0; top: 110px; width: 100%; }
  .service-grid__row { display: flex; justify-content: center; gap: 8px; font-size: 17px; line-height: 33.5px; color: var(--ink-soft); }
  .service-grid__row span::before { content: "\2022"; margin-right: 4px; }
  .card--back-light .tagline-question { top: 264px; font-size: 16px; color: var(--ink); text-transform: uppercase; }
</style>
</head>
<body>

  <!-- Front -->
  <section class="card card--front">
    <div class="athlete-figure" role="img" aria-label="Faint photo of an athlete doing a floor exercise"></div>
    <div class="brand">
      <span class="brand__disc"></span>
      <span class="brand__name">Vigor Ledger</span>
    </div>
    <div class="divider"></div>
    <div class="contact">
      <h1 class="contact__name">Marcus Obadiah Lim</h1>
      <p class="contact__role">Fitness Coach</p>
      <p class="contact__role">Corrective Exercise Specialist</p>
      <ul class="contact__list">
        <li><svg viewBox="0 0 12 12"><rect x="3" y="0.5" width="6" height="11" rx="1" fill="none" stroke="#444"/><rect x="4.3" y="2" width="3.4" height="6" fill="#444"/></svg>+65 9437 2065</li>
        <li><svg viewBox="0 0 12 12"><rect x="0.5" y="2.5" width="11" height="7.5" fill="#444"/><path d="M0.5 2.5 L6 7 L11.5 2.5" fill="none" stroke="#fff"/></svg>marcus@sgvigorledger-example.com</li>
        <li><svg viewBox="0 0 12 12"><circle cx="6" cy="6" r="5.3" fill="none" stroke="#444"/><ellipse cx="6" cy="6" rx="2.3" ry="5.3" fill="none" stroke="#444"/><path d="M0.7 6 H11.3" stroke="#444"/></svg>www.sgvigorledger-example.com</li>
      </ul>
    </div>
    <svg class="front-band" viewBox="0 0 539 12" preserveAspectRatio="none">
      <polygon points="0,0 250,0 240,12 0,12" fill="#f3d80f"/>
      <polygon points="262,0 539,0 539,12 252,12" fill="#000"/>
    </svg>
  </section>

  <!-- Back, dark -->
  <section class="card card--back-dark">
    <div class="brand">
      <span class="brand__disc"></span>
      <span class="brand__name">Vigor Ledger</span>
    </div>
    <h2 class="services-title">Services</h2>
    <ul class="service-list">
      <li>Sports Strength &amp; Conditioning</li>
      <li>Kettlebell Sport Preparation</li>
      <li>28 days Weight Loss Program</li>
      <li>Myofascial Rehab Therapy</li>
      <li>Calisthenics Training</li>
      <li>Corrective Exercises</li>
      <li>Sports/Thai Massage</li>
    </ul>
    <p class="tagline-question">What is your vigor ledger?</p>
  </section>

  <!-- Back, light -->
  <section class="card card--back-light">
    <div class="ghost-disc"></div>
    <h2 class="services-title">Services</h2>
    <div class="service-grid">
      <div class="service-grid__row"><span>Sports Strength &amp; Conditioning</span><span>Sports/Thai Massage</span></div>
      <div class="service-grid__row"><span>Kettlebell Sport Preparation</span><span>Corrective Exercises</span></div>
      <div class="service-grid__row"><span>28 days Weight Loss Program</span><span>Calisthenics Training</span></div>
      <div class="service-grid__row"><span>Myofascial Rehab Therapy</span></div>
    </div>
    <p class="tagline-question">What is your vigor ledger?</p>
  </section>

</body>
</html>
```